Dentistry Office

We want a new design for a Dentist's office website.

The theme is: "We provide high quality, state-of-the-art, dental care in a comfortable, caring environment."

The site currently has a menu on the left of the page with about 40 items on it. There is a great deal of textual content on each page, plus several illustrations.

We want to do this using CSS, so we need specifications in the CSS for all possible elements. The CSS needs to be named in a logical manner for easy use.

Every dentist on the planet seems to use lots of Flash. We don't want to because it is so distracting. We are looking for an elegant solution targeting 24-55 age group, but not excluding anyone.

The following (from another dentist's site) can give you a taste of what we want to communicate on the site:

"After 20 years of teaching dentists how to refine their technique and many years of writing textbooks, I currently devote my time to my office and the hands-on practice of dentistry. I'd like to welcome you personally to my dental practice, and I invite you to meet my highly experienced team of professionals.

"We have offered complete dental care of the highest quality since 1978. We provide Preventive Services, Tooth Whitening and Cosmetic Dentistry for a beautiful smile, Endodontics (root canal treatment) to treat painful teeth, Sedation Dentistry so you can relax, and Dental Implants to restore what is missing. We offer total care.

"Our approach to your health is simple: We use our education, experience and dedication to provide every patient with superior dental care.

"This passion for excellence is not just a goal, but a standard every member of our team holds.

"We also pride ourselves with our state of the art procedures, training and technology. This includes creating a beautiful smile using techniques that preserve as much of the original tooth as possible.

"Our abilities are renowned throughout the dental profession and I hope if you have any questions you will contact us by an e-mail note, by phone or just by dropping by."

Keep in mind the screen shape and dimensions. Your design needs to work in the normal screen proportions, regardless of how it looks when you post it here. Scrolling is OK, but the first impression needs to work.
Updates

Keep in mind that there will be about 250 words, or more, on each page.

Competitors web sites:

http://www.brindlecovedentist.example/

http://www.brindlecovedentalcare.example/

http://www.grinsbymarlowvaledental.example/

http://www.tenbyfamilydentalcare.example/

http://www.quelmardental.example/

http://www.dovrinadental.example/

We need to compete with these.

Target Market(s)

Generally adults seeking the most experienced and comfortable-to-be-with dentist.

Industry/Entity Type

Training

Requirements
Must have
• Must stand apart from other dentists.
• Must be elegant.
• Must have a horizontal menu structure across all columns, NOT a vertical that requires scrolling, no popout, pop down, etc. menus.
• We are looking for something special.
• Do not waste your time or ours putting up templates and things you have used before.
• Personally, I do not see how someone outside the US can understand the northern California dental market. But you are welcome to try.
Should not have
• Flash or graphics that move
• The look of a template
• Folksy fonts
• Looks like you used it 20 times before

```html
<!DOCTYPE html>
<html lang="en">
<head>
<meta charset="utf-8">
<title>Brindle Cove Dentist</title>
<link href="https://fonts.googleapis.com/css2?family=Noto+Sans:wght@400;600;700&display=swap" rel="stylesheet">
<style>
:root{
  --slate:#646e7d;
  --slate-dark:#4a5563;
  --slate-deep:#3e4855;
  --panel:#e9ebee;
  --page:#f7f7f7;
  --ink:#3f4650;
  --heading:#3b4a55;
  --white:#ffffff;
  --tick:#5a6675;
  --promo:#dcd9c4;
}
*{margin:0;padding:0;box-sizing:border-box}
html,body{width:886px;height:1200px;overflow:hidden}
body{background:var(--page);font-family:"Noto Sans",sans-serif;color:var(--ink);position:relative}
.abs{position:absolute}

/* header */
.masthead{left:0;top:0;width:886px;height:253px;background:linear-gradient(180deg,#6f7b8a 0%,#56626f 55%,#4a5562 100%);overflow:hidden}
.masthead-photo{right:66px;top:8px;width:340px;height:245px;background:radial-gradient(ellipse at 60% 55%,#e8dcd2 0%,#c9b3a4 35%,#6d7683 75%,rgba(86,98,111,0) 100%)}
.call-tab{left:72px;top:0;width:330px;height:32px;background:linear-gradient(180deg,#f4f4f4,#dfe1e3);border-bottom-right-radius:14px;font-size:15px;color:#555;padding:10px 0 0 28px;letter-spacing:.3px}
.site-title{left:83px;top:104px;color:var(--white);font-size:31px;line-height:36px;font-weight:600;text-shadow:0 1px 3px rgba(0,0,0,.45);letter-spacing:.5px}

/* nav */
.main-nav{left:0;top:253px;width:886px;height:33px;background:var(--slate);display:flex;align-items:center;padding-left:72px}
.main-nav a{color:var(--white);font-size:12px;font-weight:700;text-decoration:none;padding:0 16px;line-height:20px;border-right:1px solid #4f5967;letter-spacing:.3px}
.main-nav a:last-child{border-right:none}
.main-nav a.current{background:var(--white);color:var(--slate-dark);height:33px;line-height:33px;padding:0 14px;border-right:none}

/* sidebar */
.sidebar{left:73px;top:310px;width:175px;height:802px;background:var(--panel)}
.side-head{height:22px;background:var(--slate);color:var(--white);font-size:12px;font-weight:700;letter-spacing:.6px;padding:3px 0 0 12px;border-bottom:2px solid #c8ccd2}
.side-list{list-style:none;padding:9px 0 6px 0}
.side-list li{font-size:10px;line-height:17.7px;padding-left:21px;position:relative;color:#454c55}
.side-list li::before{content:"";position:absolute;left:9px;top:6px;border-left:3px solid #7a8390;border-top:3px solid transparent;border-bottom:3px solid transparent}

/* main */
.section-title{font-size:16px;color:var(--heading);font-weight:400;letter-spacing:.3px}
.welcome-text{left:272px;top:338px;width:356px;font-size:9.6px;line-height:14.5px;color:#444}
.welcome-photo{left:637px;top:341px;width:176px;height:132px;border:2px solid #d6d9dc;background:linear-gradient(180deg,#7f9a6a 0%,#8b7a66 45%,#6e6a5e 70%,#a8a8a4 100%)}
.btn-learn{left:538px;top:453px;width:88px;height:19px;border-radius:3px;background:linear-gradient(180deg,#7c8693,#5b6574);color:var(--white);font-size:9px;font-weight:700;line-height:19px;padding-left:9px;letter-spacing:.3px}
.provides{left:272px;top:529px;list-style:none}
.provides li{font-size:9.6px;line-height:17.7px;padding-left:18px;position:relative;color:#444}
.provides svg{position:absolute;left:0;top:4px}

/* promo */
.promo{left:278px;top:712px;width:507px;height:151px;border:2px solid #7d8590;border-radius:5px;background:linear-gradient(180deg,#e6e4d6,var(--promo));overflow:hidden}
.promo-photo{right:0;top:0;width:185px;height:149px;background:radial-gradient(ellipse at 55% 50%,#e7c7a8 0%,#cfa37f 30%,#b7b4a0 65%,rgba(220,217,196,0) 100%)}
.promo-line{left:12px;font-size:16.5px;color:#3d4147;letter-spacing:.4px}
.promo-more{left:242px;top:90px;font-size:10px;color:#555;letter-spacing:.4px}
.promo-note{left:0;bottom:0;width:505px;height:36px;background:linear-gradient(90deg,rgba(90,98,108,.95),rgba(90,98,108,.55));color:var(--white);font-size:9px;line-height:14px;padding:4px 0 0 8px;letter-spacing:.3px}

/* info buttons */
.info-btn{left:278px;width:203px;height:33px;border-radius:4px;background:linear-gradient(90deg,#5e6877 0%,#6f7987 60%,#c9ccd1 100%);color:var(--white);font-size:14px;line-height:33px;padding-left:17px;letter-spacing:.3px}
.info-btn svg{position:absolute;right:6px;top:-10px}
.call-card{left:278px;top:1060px;width:203px;height:51px;background:#eceef0;border-radius:0 0 4px 4px;font-size:9.4px;line-height:14.5px;padding:4px 0 0 6px;letter-spacing:.4px;color:#333}

/* map */
.map-title{left:543px;top:873px;font-size:14.5px;font-weight:700;color:#3d4147;letter-spacing:.3px}
.map-box{left:539px;top:897px;width:245px;height:220px;border:2px solid #cfd1d2;background:linear-gradient(160deg,#e6e6e2,#d9d9d4)}

/* footer */
.site-footer{left:0;top:1137px;width:886px;height:63px;background:var(--slate)}
.footer-links{left:87px;top:11px;font-size:9.6px;color:var(--white)}
.footer-copy{left:87px;top:35px;font-size:9.6px;color:var(--white)}
.to-top{left:732px;top:0;width:50px;height:25px;background:var(--white);color:#6d8aa6;font-size:11px;text-align:center;line-height:25px}
</style>
</head>
<body>

<header class="masthead abs">
  <div class="masthead-photo abs" role="img" aria-label="Photo of a joyful woman raising her arms"></div>
  <div class="call-tab abs">Call for Appointments: (555) 014-2286.</div>
  <h1 class="site-title abs">Brindle Cove Dentist<br>Owen Tessler, DDS, FAGD</h1>
</header>

<nav class="main-nav abs">
  <a class="current">Home</a>
  <a>Why we are differnt</a>
  <a>Technologies we offer</a>
  <a>Meet Dr.Tessler</a>
  <a>Our Staff</a>
  <a>Contact Us</a>
  <a>Links</a>
</nav>

<aside class="sidebar abs">
  <div class="side-head">EDUCATION</div>
  <ul class="side-list">
    <li>Emergency Dental Care</li><li>Your Mouth</li><li>Your Tooth</li><li>Cracked Tooth?</li><li>Missing a Tooth?</li><li>Sensitive Teeth</li><li>Dry MouthTooth</li><li>GrindingSleep</li><li>Dentistry</li><li>Videos</li>
  </ul>
  <div class="side-head">PREVENTATIVE</div>
  <ul class="side-list">
    <li>What is Preventive Care?</li><li>Taking Care of Your Teeth</li><li>Eating Right</li><li>Dental Check-Ups Sealants</li><li>Periodontal Disease</li><li>Kicking the Habit</li><li>Night Guards</li><li>Dental X-Rays</li><li>Antibiotics with Treatment</li>
  </ul>
  <div class="side-head">COSMETICS</div>
  <ul class="side-list">
    <li>Cosmetic Dentistry</li><li>Bleaching and Whitening</li><li>Cosmetic Bonding</li><li>Esthetic Veneers</li><li>Tooth Shaping</li>
  </ul>
  <div class="side-head">RESTORATIONS</div>
  <ul class="side-list">
    <li>Crowns/Caps: Each Step</li><li>CMBRs</li><li>Porcelain Bridges</li><li>Bonded Dental Bridges</li><li>Gold Restorations Implants</li><li>Treating CrackedTeeth</li><li>Periodontal (gum) Treatment</li>
  </ul>
  <div class="side-head">VISITING OUR OFFICE</div>
  <ul class="side-list">
    <li>Where to Stay</li><li>First Visit / Map</li><li>Financial Policy</li><li>Dental Insurance</li>
  </ul>
</aside>

<h2 class="section-title abs" style="left:273px;top:309px">Welcome</h2>
<p class="welcome-text abs">Lorem ipsum dolor sit amet, consectetuer adipiscing elit. Aenean commodo ligula eget dolor. Aenean massa. Cum sociis natoque penatibus et magnis dis parturient montes, nascetur ridiculus mus. Doneuam felis, ultricies nec, pellentesque eu, pretium quis, sem. Nulla consequat massa quis enim. Donec pede justo, fringilla vel, aliquet nec, vulputate eget, arcu. In enim justo, rhoncus ut, imperdiet a, venenatis vitae, justo.massa quis enim. Donec pede justo,&nbsp; pretium quis, sem. Nulla consequat massa quis enim. Donec pede justo, fringilla vel,</p>
<div class="welcome-photo abs" role="img" aria-label="Photo of the dental office building among trees"></div>
<div class="btn-learn abs">Learn more &#9656;&#9656;</div>

<h2 class="section-title abs" style="left:274px;top:497px">Dr. Tessler Provides</h2>
<ul class="provides abs">
  <li><svg width="11" height="10" viewBox="0 0 11 10"><path d="M1 5.5 L4 8.5 L10 1" fill="none" stroke="#5a6675" stroke-width="2.2"/></svg>General dentistry—oral hygiene, cavity detection and repair, crowns.</li>
  <li><svg width="11" height="10" viewBox="0 0 11 10"><path d="M1 5.5 L4 8.5 L10 1" fill="none" stroke="#5a6675" stroke-width="2.2"/></svg>Cosmetic/restorative dentistry—broken or misshapen teeth, crooked smiles, unsightly gaps</li>
  <li><svg width="11" height="10" viewBox="0 0 11 10"><path d="M1 5.5 L4 8.5 L10 1" fill="none" stroke="#5a6675" stroke-width="2.2"/></svg>Non-metal fillings—nontoxic, durable tooth-colored resin fillings that are proven to provide better results</li>
  <li><svg width="11" height="10" viewBox="0 0 11 10"><path d="M1 5.5 L4 8.5 L10 1" fill="none" stroke="#5a6675" stroke-width="2.2"/></svg>Tooth shaping—extending, shortening or otherwise reshaping teeth for improved esthetics</li>
  <li><svg width="11" height="10" viewBox="0 0 11 10"><path d="M1 5.5 L4 8.5 L10 1" fill="none" stroke="#5a6675" stroke-width="2.2"/></svg>Complete smile make-over's—resin veneers that reshape the whole mouth while preserving natural teeth</li>
  <li><svg width="11" height="10" viewBox="0 0 11 10"><path d="M1 5.5 L4 8.5 L10 1" fill="none" stroke="#5a6675" stroke-width="2.2"/></svg>Tooth whitening—at-home bleaching options to make teeth appear years younger</li>
  <li><svg width="11" height="10" viewBox="0 0 11 10"><path d="M1 5.5 L4 8.5 L10 1" fill="none" stroke="#5a6675" stroke-width="2.2"/></svg>Laser Dentistry, Sleep Dentistry, and Implant Dentistry with the Finest and Latest Equipment and Materials.</li>
  <li><svg width="11" height="10" viewBox="0 0 11 10"><path d="M1 5.5 L4 8.5 L10 1" fill="none" stroke="#5a6675" stroke-width="2.2"/></svg>Dental Implants to replace missing teeth.</li>
  <li><svg width="11" height="10" viewBox="0 0 11 10"><path d="M1 5.5 L4 8.5 L10 1" fill="none" stroke="#5a6675" stroke-width="2.2"/></svg>Sedation Dentistry so you can be relaxed.</li>
</ul>

<section class="promo abs">
  <div class="promo-photo abs" role="img" aria-label="Photo of a smiling young couple outdoors"></div>
  <p class="promo-line abs" style="top:18px">We offer an Initial Patient Examination</p>
  <p class="promo-line abs" style="top:47px">X-rays and Cleaning for $79.00.</p>
  <p class="promo-more abs">Learn More</p>
  <p class="promo-note abs">New patients only. Offers are cash patients only.<br>Insurance will be billed at full value.</p>
</section>

<div class="info-btn abs" style="top:897px">Office Hours
  <svg width="40" height="40" viewBox="0 0 40 40"><circle cx="20" cy="20" r="17" fill="#f2b233"/><circle cx="20" cy="20" r="13" fill="#fff"/><path d="M20 10 V20 H27" stroke="#333" stroke-width="2" fill="none"/></svg>
</div>
<div class="info-btn abs" style="top:962px">Where to stay?
  <svg width="40" height="40" viewBox="0 0 40 40"><circle cx="20" cy="20" r="17" fill="#fff"/><circle cx="20" cy="20" r="14" fill="#2a7fd6"/><text x="20" y="27" font-size="19" font-weight="700" fill="#fff" text-anchor="middle" font-family="Noto Sans, sans-serif">?</text></svg>
</div>
<div class="info-btn abs" style="top:1028px;border-radius:4px 4px 0 0">Please call
  <svg width="40" height="44" viewBox="0 0 40 44"><path d="M30 4 C22 2 16 14 16 24 C16 32 20 38 26 40 L30 34 L25 30 C23 26 24 18 27 14 L33 14 Z" fill="#d12b22"/></svg>
</div>
<p class="call-card abs">contact us outside office hours for an emergency, please call at<br>(555) 018-4473.</p>

<h2 class="map-title abs">Map to Office</h2>
<div class="map-box abs" role="img" aria-label="Street map showing the route to the office"></div>

<footer class="site-footer abs">
  <p class="footer-links abs">Brindle Cove Dentist • Tell A Friend • Privacy &amp; Legal • Dental Resources • New Patient Forms</p>
  <p class="footer-copy abs">Copyright © 2009. All Rights Reserved</p>
  <div class="to-top abs">Top</div>
</footer>

</body>
</html>
```